Business Card Design for Occupational Medicine Start Up Company

We need to design a professional business card. We are a healthcare company providing occupational medicine services to blue collar industries. We are professional, efficient and high quality service providers.

Target Market(s)

Blue Collar Industry: Shipbuilding, Ports, Trucking Companies; The Executives and Safety Officers for these companies

Industry/Entity Type

Healthcare

Contact Information for Business Card

Logo, Name, Title, Email, Phone

Other font styles liked:
• Please match our Brand Guide

Requirements
Must have
• Our Company Colors and Logo

```html
<!DOCTYPE html>
<html lang="en">
<head>
<meta charset="utf-8">
<title>SteadyCrew Business Card</title>
<link href="https://fonts.googleapis.com/css2?family=Montserrat:wght@600;700&family=Roboto:wght@400&display=swap" rel="stylesheet">
<style>
  :root {
    --navy: #283a86;
    --navy-deep: #1f2f73;
    --white: #ffffff;
    --ink: #1c1c28;
    --sky: #2aa3df;
    --amber: #f2a53a;
    --stage: #e7e8ec;
  }
  * { margin: 0; padding: 0; box-sizing: border-box; }
  html, body {
    width: 1200px; height: 900px; overflow: hidden;
    background: var(--stage);
  }
  .canvas {
    position: relative; width: 1200px; height: 900px;
  }
  .card {
    position: absolute; left: 320px; width: 560px; height: 320px;
    border-radius: 18px; overflow: hidden;
    box-shadow: 0 6px 18px rgba(0,0,0,0.15);
  }
  .card-front { top: 90px; background: var(--white); }
  .card-back { top: 470px; background: var(--navy); }

  .brand {
    position: absolute; display: flex; align-items: center; gap: 10px;
    font-family: "Montserrat", sans-serif; font-weight: 700;
    letter-spacing: 0.04em; text-transform: uppercase;
  }
  .brand-dot { border-radius: 50%; flex: none; }
  .card-front .brand {
    left: 64px; top: 52px; font-size: 26px; color: var(--navy);
  }
  .card-front .brand-dot { width: 18px; height: 18px; background: var(--sky); }

  .contact {
    position: absolute; left: 40px; bottom: 46px;
    font-family: "Roboto", sans-serif; font-size: 15px; color: var(--ink);
    list-style: none; line-height: 1.55;
  }
  .contact li { display: flex; align-items: center; gap: 8px; }
  .contact svg { width: 13px; height: 13px; fill: var(--navy); flex: none; }

  .person {
    position: absolute; right: 64px; bottom: 42px; text-align: right;
  }
  .person-name {
    font-family: "Montserrat", sans-serif; font-weight: 700;
    font-size: 26px; color: var(--navy); letter-spacing: 0.02em;
    text-transform: uppercase;
  }
  .person-title {
    font-family: "Roboto", sans-serif; font-size: 15px; color: var(--ink);
  }
  .corner-block {
    position: absolute; right: 0; bottom: 30px;
    width: 36px; height: 52px; background: var(--navy);
  }

  .card-back .brand {
    left: 50%; top: 50%; transform: translate(-50%, -50%);
    font-size: 38px; color: var(--white);
  }
  .card-back .brand-dot { width: 26px; height: 26px; background: var(--amber); }
</style>
</head>
<body>
<main class="canvas">
  <section class="card card-front" aria-label="Card front">
    <div class="brand"><span class="brand-dot"></span>SteadyCrew</div>

    <ul class="contact">
      <li>
        <svg viewBox="0 0 24 24" aria-hidden="true"><path d="M6.6 10.8a15.1 15.1 0 0 0 6.6 6.6l2.2-2.2c.3-.3.7-.4 1-.2 1.1.4 2.3.6 3.6.6.6 0 1 .4 1 1V20c0 .6-.4 1-1 1A17 17 0 0 1 3 4c0-.6.4-1 1-1h3.5c.6 0 1 .4 1 1 0 1.3.2 2.5.6 3.6.1.3 0 .7-.2 1z"/></svg>
        (555)214 3098
      </li>
      <li>
        <svg viewBox="0 0 24 24" aria-hidden="true"><path d="M2 5h20v14H2z M3 6l9 7 9-7" fill="none" stroke="#283a86" stroke-width="2"/></svg>
        hello@steadycrew.com
      </li>
      <li>
        <svg viewBox="0 0 24 24" aria-hidden="true"><circle cx="12" cy="12" r="10"/></svg>
        www.steadycrew.com
      </li>
    </ul>

    <div class="person">
      <p class="person-name">Daniel Reyes</p>
      <p class="person-title">Director</p>
    </div>
    <div class="corner-block"></div>
  </section>

  <section class="card card-back" aria-label="Card back">
    <div class="brand"><span class="brand-dot"></span>SteadyCrew</div>
  </section>
</main>
</body>
</html>
```